Help design website for "Brightwater Civic Advisors" to advance the common good

Here is the Google doc link that lays out the design:

https://files.plumrivet.example/sheet/d/7QmTzR2wLx9KpVbN4hJcY8sEaUoFdG3iXkMnPq5rWt6/edit?usp=sharing

Here is the Google drive folder with the logos and photos: https://vault.plumrivet.example/open?id=4HkWp9LzQe2TxRvN8mBaYc3DsUoJfG6

The testimonials are being gathered and will be shared by Friday, 1/4.

The winner will also have to migrate the coding files to my hosting site.

Thank you for your help! Looking forward to seeing your designs.

Target Market(s)

Prospective clients

Industry/Entity Type

Non Profit

Coding

Coded - Design and coding required

Number of Pages Required

5+ page

Requirements
Must have
• Noted in the Google doc regarding layout.
Nice to have

```html
<!DOCTYPE html>
<html lang="en">
<head>
<meta charset="utf-8">
<title>Media &amp; Impact — Brightwater Civic Advisors</title>
<link href="https://fonts.googleapis.com/css2?family=Poppins:wght@400;500;600;700;800&family=Montserrat:wght@500&display=swap" rel="stylesheet">
<style>
  :root {
    --brand-blue: #3d8bcd;
    --ink: #111111;
    --white: #ffffff;
    --footer-bg: #252630;
    --pattern-bg: #f3f3f4;
    --divider: #4a4c58;
  }
  * { box-sizing: border-box; margin: 0; padding: 0; }
  html, body { width: 950px; height: 1200px; overflow: hidden; background: var(--white); }
  body { font-family: "Poppins", sans-serif; color: var(--ink); }
  .page { position: relative; width: 950px; height: 1200px; overflow: hidden; }

  .site-header { position: absolute; inset: 0 0 auto 0; height: 98px; background: var(--brand-blue); z-index: 3; }
  .brand { position: absolute; left: 114px; top: 22px; display: flex; align-items: center; gap: 12px; }
  .brand-square { width: 46px; height: 46px; background: var(--white); flex: none; }
  .brand-name { font-family: "Montserrat", sans-serif; font-weight: 500; color: var(--white); font-size: 15px; letter-spacing: 4px; line-height: 18px; text-transform: uppercase; width: 240px; }
  .cta-button { position: absolute; left: 582px; top: 16px; width: 253px; height: 33px; border: 2px solid var(--white); color: var(--white); font-weight: 700; font-size: 11px; display: flex; align-items: center; justify-content: center; text-decoration: none; }
  .main-nav { position: absolute; top: 70px; right: 115px; display: flex; gap: 21px; }
  .main-nav a { color: var(--white); font-weight: 700; font-size: 11px; text-decoration: none; padding-bottom: 2px; }
  .main-nav a.is-current { border-bottom: 1px solid var(--white); }

  .hero { position: absolute; left: 0; top: 98px; width: 950px; height: 444px;
    background: linear-gradient(180deg, #1b1a1c 0%, #3a2a22 40%, #6b4d2e 62%, #a88f3a 82%, #7a6a30 100%); }
  .hero-edge { position: absolute; left: 0; top: 0; z-index: 2; }

  .section-title { position: absolute; z-index: 4; top: 505px; left: 0; width: 950px; text-align: center; font-weight: 800; font-size: 26px; line-height: 36px; color: var(--ink); }
  .section-rule { position: absolute; z-index: 4; top: 546px; left: 464px; width: 22px; height: 3px; background: var(--brand-blue); }

  .podcast-card { position: absolute; top: 601px; width: 346px; height: 282px; color: var(--white); overflow: hidden; }
  .podcast-card--left { left: 113px; background: linear-gradient(160deg, #2a1a14 0%, #3e2a20 55%, #120d0b 100%); }
  .podcast-card--right { left: 487px; background: linear-gradient(180deg, #8a8a82 0%, #5c6048 45%, #2e3128 100%); }
  .podcast-card::after { content: ""; position: absolute; inset: 0; background: linear-gradient(180deg, rgba(0,0,0,0) 45%, rgba(0,0,0,0.55) 100%); }
  .mic-icon { position: absolute; left: 22px; top: 168px; z-index: 1; }
  .podcast-caption { position: absolute; left: 16px; right: 20px; top: 227px; z-index: 1; font-weight: 700; font-size: 12.6px; line-height: 14.5px; text-transform: uppercase; }

  .pattern-band { position: absolute; top: 892px; left: 0; width: 950px; height: 140px; background: var(--pattern-bg); }
  .site-footer { position: absolute; left: 0; top: 0; width: 950px; height: 1200px; pointer-events: none; }
  .footer-brand { position: absolute; left: 113px; top: 1078px; display: flex; align-items: center; gap: 14px; }
  .footer-brand .brand-square { background: var(--brand-blue); width: 60px; height: 60px; }
  .footer-brand .brand-name { font-size: 18px; line-height: 24px; letter-spacing: 4px; width: 280px; }
  .footer-divider { position: absolute; left: 482px; top: 1046px; width: 1px; height: 112px; background: var(--divider); }
  .footer-menu-title { position: absolute; left: 530px; top: 1060px; color: var(--white); font-weight: 700; font-size: 9.5px; }
  .footer-links { position: absolute; left: 530px; top: 1087px; color: var(--white); font-size: 9.5px; display: flex; gap: 8px; }
  .footer-links a { color: var(--white); text-decoration: none; }
  .footer-copy { position: absolute; left: 531px; top: 1135px; color: var(--white); font-size: 9px; }
</style>
</head>
<body>
<div class="page">
  <header class="site-header">
    <div class="brand">
      <span class="brand-square"></span>
      <span class="brand-name">Brightwater Civic Advisors</span>
    </div>
    <a class="cta-button" href="#">BOOK A COMPLIMENTARY CONSULTATION</a>
    <nav class="main-nav">
      <a href="#">ABOUT</a>
      <a href="#">SERVICES &amp; TESTIMONIALS</a>
      <a href="#" class="is-current">MEDIA &amp; IMPACT</a>
      <a href="#">CONTACT</a>
    </nav>
  </header>

  <div class="hero" role="img" aria-label="Photo of a speaker at a podium addressing an auditorium of students in yellow and blue shirts"></div>
  <svg class="hero-edge" width="950" height="560" viewBox="0 0 950 560" aria-hidden="true">
    <polygon points="0,518 475,449 950,518 950,560 0,560" fill="var(--brand-blue)"/>
    <polygon points="0,532 475,457 950,532 950,560 0,560" fill="var(--white)"/>
  </svg>

  <h1 class="section-title">Podcasts</h1>
  <div class="section-rule"></div>

  <article class="podcast-card podcast-card--left" role="img" aria-label="Photo of a speaker at a podium with a microphone">
    <svg class="mic-icon" width="38" height="54" viewBox="0 0 38 54" aria-hidden="true">
      <rect x="10" y="0" width="18" height="32" rx="9" fill="#fff"/>
      <path d="M4 22 a15 15 0 0 0 30 0" fill="none" stroke="#fff" stroke-width="3.5"/>
      <rect x="17" y="37" width="4" height="11" fill="#fff"/>
      <rect x="9" y="48" width="20" height="4" rx="2" fill="#fff"/>
    </svg>
    <p class="podcast-caption">Dana discusses with the Lakeview Ledger student newspaper the goals for the MLK Day of Service</p>
  </article>

  <article class="podcast-card podcast-card--right" role="img" aria-label="Group photo of students standing outdoors in front of a columned building">
    <svg class="mic-icon" width="38" height="54" viewBox="0 0 38 54" aria-hidden="true">
      <rect x="10" y="0" width="18" height="32" rx="9" fill="#fff"/>
      <path d="M4 22 a15 15 0 0 0 30 0" fill="none" stroke="#fff" stroke-width="3.5"/>
      <rect x="17" y="37" width="4" height="11" fill="#fff"/>
      <rect x="9" y="48" width="20" height="4" rx="2" fill="#fff"/>
    </svg>
    <p class="podcast-caption">Dana speaks about ways students can get involved with Chicago South Side neighborhoods.</p>
  </article>

  <div class="pattern-band"></div>

  <footer>
    <svg class="site-footer" width="950" height="1200" viewBox="0 0 950 1200" aria-hidden="true">
      <polygon points="0,1028 474,946 950,1028 950,1200 0,1200" fill="var(--footer-bg)"/>
    </svg>
    <div class="footer-brand">
      <span class="brand-square"></span>
      <span class="brand-name">Brightwater Civic Advisors</span>
    </div>
    <div class="footer-divider"></div>
    <p class="footer-menu-title">MENU</p>
    <nav class="footer-links">
      <a href="#">ABOUT</a><span>|</span>
      <a href="#">SERVICES &amp; TESTIMONIALS</a><span>|</span>
      <a href="#">MEDIA &amp; IMPACT</a><span>|</span>
      <a href="#">CONTACT</a>
    </nav>
    <p class="footer-copy">Copyrights @ 2019 All Rights Reserved</p>
  </footer>
</div>
</body>
</html>
```